Family business needs stationery redesign with new logo

Family owned company, established in 1987 wanting a brand 'refresh'. We are an electrical, refrigeration and construction company based in the Barkly Region Northern Territory, Australia. We have a new logo we would like to use which is uploaded along with our current letterhead and email signature. We are also dropping the word 'contractors' so please do not include this on any designs. Please note also, the 'orange' color used in our logo and designs should be Northern Territory red ochre which is as follows:

RGB (Hex): #C75B12
PantoneĀ® 159 C
CMYK: 1 / 74 / 100 / 7

We are needing our stationery redesigned using our new logo. Please include letterheads, business cards, envelopes, and email signatures.

We currently use our business letterheads for quotations, invoices, letters, HR matters, and internal memos.

We also need a separate simplified letterhead for internal paperwork such as employee leave forms, meeting agendas, and meeting minutes etc.

Reason: Needing more submissions of full package designs. We are wanting all our stationery, including business cards, letterheads, email signatures, envelopes, etc to be cohesive. We also require ALL the information, as supplied on our template letterhead, to be included on the new letterhead designs. including electrical license no.etc Thank you, R&W

Reason: needing more time as work has got in the way of looking over designs. A lot of designs not meeting the brief/criteria.

Industry/Entity Type

Business

Colors
0355a3
f37122

Requirements
Must have
• The 'orange' color used in the designs should be Northern Territory red ochre which is as follows:
• RGB (Hex): #C75B12
• PantoneĀ® 159 C
• CMYK: 1 / 74 / 100 / 7
• ***MUST INCLUDE ALL INFORMATION THAT IS ON OUR CURRENT LETTERHEAD***
Should not have
• Please do not include the word 'contractors'

```html
<!DOCTYPE html>
<html lang="en">
<head>
<meta charset="utf-8">
<title>R&amp;W Business Cards</title>
<link href="https://fonts.googleapis.com/css2?family=Arimo:wght@400;700&family=Open+Sans:wght@400&display=swap" rel="stylesheet">
<style>
  :root {
    --navy: #1b3170;
    --ochre: #c75b12;
    --white: #ffffff;
    --ink: #4a4a4a;
    --rule: #c9c9c9;
    --backdrop: #e4e4e4;
  }
  * { margin: 0; padding: 0; box-sizing: border-box; }
  html, body {
    width: 1200px; height: 856px; overflow: hidden;
    background: var(--backdrop);
    font-family: "Arimo", Arial, sans-serif;
  }
  .stage { position: relative; width: 1200px; height: 856px; }

  .card {
    position: absolute;
    width: 525px; height: 300px;
    border-radius: 16px;
    overflow: hidden;
    transform: scale(1.0165);
    transform-origin: top left;
  }
  .card--front { left: 335px; top: 113px; background: var(--white); }
  .card--back-light { left: 57px; top: 438px; background: var(--navy); }
  .card--back-ochre { left: 613px; top: 438px; background: var(--navy); }

  .swoosh { position: absolute; inset: 0; width: 100%; height: 100%; }

  .wordmark {
    position: absolute;
    font-family: "Arimo", Arial, sans-serif;
    font-weight: 700;
    white-space: nowrap;
    transform: translate(-50%, -50%);
    line-height: 1;
  }
  .card--front .wordmark { left: 132px; top: 159px; font-size: 60px; color: var(--navy); }
  .card--back-light .wordmark,
  .card--back-ochre .wordmark { left: 50%; top: 143px; font-size: 92px; color: var(--white); }

  .divider {
    position: absolute; left: 258px; top: 58px;
    width: 1px; height: 196px; background: var(--rule);
  }

  .contact { position: absolute; left: 292px; top: 68px; color: var(--ink); }
  .contact__name { font-size: 19px; font-weight: 700; color: var(--navy); letter-spacing: 0.2px; }
  .contact__role { font-size: 14.5px; color: var(--ochre); margin-top: 2px; }
  .contact__address { font-size: 13.5px; line-height: 17px; margin-top: 10px; }
  .contact__list { list-style: none; margin-top: 12px; font-size: 13.5px; }
  .contact__list li { display: flex; align-items: center; height: 20px; }
  .contact__list svg { width: 12px; height: 12px; margin-right: 8px; fill: var(--navy); flex: none; }

  .established {
    position: absolute; left: 0; right: 0; top: 244px;
    text-align: center;
    font-family: "Open Sans", Arial, sans-serif;
    font-size: 19px; letter-spacing: 0.5px;
  }
  .card--back-light .established { color: var(--white); }
  .card--back-ochre .established { color: var(--ochre); }
</style>
</head>
<body>
<main class="stage">

  <section class="card card--front" aria-label="Business card front">
    <svg class="swoosh" viewBox="0 0 525 300" preserveAspectRatio="none" aria-hidden="true">
      <path d="M0,221 Q220,268 525,274 L525,279 Q220,275 0,238 Z" fill="var(--ochre)"/>
      <path d="M0,243 Q220,281 525,284 L525,300 L0,300 Z" fill="var(--navy)"/>
    </svg>
    <div class="wordmark">R&amp;W</div>
    <div class="divider"></div>
    <div class="contact">
      <div class="contact__name">DANIEL REEVE</div>
      <div class="contact__role">CEO/Founder</div>
      <div class="contact__address">214 Dunmore Street<br>Tennant Creek, NT 0860</div>
      <ul class="contact__list">
        <li><svg viewBox="0 0 12 12"><path d="M2.5 0.5 L4.5 0.5 L5.3 3.2 L3.9 4.3 Q5 6.9 7.7 8.1 L8.8 6.7 L11.5 7.5 L11.5 9.5 Q11.5 11.5 9.5 11.5 Q0.5 10.5 0.5 2.5 Q0.5 0.5 2.5 0.5 Z"/></svg>08 8962 4410</li>
        <li><svg viewBox="0 0 12 12"><rect x="3" y="0.5" width="6" height="3.5"/><rect x="0.5" y="4.5" width="11" height="5" rx="1"/><rect x="2.5" y="10" width="7" height="1.5"/></svg>08 8962 4411</li>
        <li><svg viewBox="0 0 12 12"><path d="M0.5 2 L11.5 2 L11.5 10 L0.5 10 Z M1.5 3 L6 6.5 L10.5 3 Z" fill-rule="evenodd"/></svg>office@rwbarkly.com</li>
        <li><svg viewBox="0 0 12 12"><circle cx="6" cy="6" r="5.5"/><path d="M3 3 Q5 4 4.5 6 Q6.5 7 6 9.5 M8 2.5 Q7.5 4.5 9.5 5" stroke="var(--white)" stroke-width="1" fill="none"/></svg>www.rwbarkly.com</li>
      </ul>
    </div>
  </section>

  <section class="card card--back-light" aria-label="Business card back, white date">
    <div class="wordmark">R&amp;W</div>
    <p class="established">Est. 1987</p>
  </section>

  <section class="card card--back-ochre" aria-label="Business card back, ochre date">
    <div class="wordmark">R&amp;W</div>
    <p class="established">Est. 1987</p>
  </section>

</main>
</body>
</html>
```